Coralpeak Dynamics Wordpress / Web Design - Agile Coaching

UPDATE: PLEASE USE MORE ICONS/GRAPHICS THEN PHOTOS. THANK YOU!

We need a web design for a new company called Coralpeak Dynamics. We do agile coaching, consulting, training and facilitation for medium to large enterprise, most just starting their agile journey. We want to be professional, but light and whimsical. We have started loading content onto the www.coralpeakdynamics.example website, using the Vantor Theme (real flexibility!)

We have a logo, and I really liked it, although if needed the colors can be adjusted depending on the design. I would advice sticking with the logo and its colors unless they become problematic or you have a fantastic idea.

I really like the colors found on post it notes, and use post it notes in all my coaching and training. I want to warn though, I don't want the whole site to be splashes of color, but I would like some pop of color, and you could use the post it note colors and the idea of post it notes for icon designs or sparingly for emphasis, but keep the design simple with lots of white space. I'm inspired by this template from Pixel Bazaars and use the power point in the 2nd attached file...this may inspire you.

I have another contest running right now, if you want to check that out as well, but it isn't necessary. Contest is titled "Coralpeak Dynamics: Software Development Consultancy Needs a Business Card Design"

Target Market(s)

medium to large software companies needing to improve the speed, quality and value of their software delivery

Industry/Entity Type

Information Technology

Number of Pages Required

3 page

Font styles to use
Sans Serif

Requirements
Must have
• Simple, easy to use, easy navigation, space!
• content on my front page is accurate so should be included www.coralpeakdynamics.example
• 2nd page you can look at is http://www.coralpeakdynamics.example/inspiration/
• 3rd page you can look at is http://www.coralpeakdynamics.example/reference-list/ (about twice as many links are going to be added in next two days!)
Nice to have
• take a look at any other page on the site. if something is password protected, use the word "password" as the password.
• Update: I like less pictures, more graphics.
Should not have
• too crowded. hard to navigate. childish graphics. too boring and corporate. :)

```html
<!DOCTYPE html>
<html lang="en">
<head>
<meta charset="utf-8">
<title>Coralpeak Dynamics – Agile Coaching</title>
<link rel="stylesheet" href="https://fonts.googleapis.com/css2?family=Open+Sans:wght@400;600;700&display=swap">
<style>
:root{
  --blue:#2a8fd0;
  --navy:#1d3f5e;
  --navy-deep:#142f48;
  --ink:#3a3f45;
  --muted:#8a9097;
  --line:#e3e6ea;
  --soft:#f5f6f8;
  --red:#e8384f;
  --purple:#8e5bb5;
  --green:#8cc63f;
  --sky:#2a9fe0;
  --white:#ffffff;
}
*{box-sizing:border-box;margin:0;padding:0}
html,body{width:1200px;height:2380px;overflow:hidden}
body{font-family:"Open Sans",Arial,sans-serif;color:var(--ink);background:var(--white);font-size:13px;line-height:1.6}
.wrap{width:1000px;margin:0 auto;position:relative}

/* header */
.site-header{height:130px;border-bottom:1px solid var(--line)}
.site-header .wrap{display:flex;align-items:center;justify-content:space-between;height:130px}
.brand{display:flex;align-items:center;gap:12px;font-size:22px;font-weight:700;color:var(--navy)}
.brand-dot{width:38px;height:38px;border-radius:50%;background:var(--blue)}
.main-nav{display:flex;gap:4px}
.main-nav a{font-size:11px;font-weight:600;color:var(--ink);text-decoration:none;padding:10px 14px;letter-spacing:.5px}
.main-nav a.active{border-top:3px solid var(--blue);color:var(--blue)}

/* hero */
.hero{height:500px;position:relative;background:linear-gradient(100deg,#1f2a3a 0%,#2e3d52 35%,#8e8a86 60%,#c9c4bd 100%)}
.hero-photo{position:absolute;inset:0}
.hero-title{position:absolute;left:130px;top:170px;color:var(--white)}
.hero-title h1{font-size:50px;font-weight:700;letter-spacing:1px;line-height:1.1}
.hero-title p{font-size:32px;font-weight:400;line-height:1.2}
.hero-arrow{position:absolute;top:236px;width:28px;height:28px;fill:var(--white)}
.hero-arrow.prev{left:14px}.hero-arrow.next{right:14px}

/* welcome */
.welcome{height:190px;text-align:center;padding-top:44px}
.welcome h2{font-size:30px;font-weight:400;color:var(--ink)}
.welcome h2 span{color:var(--blue)}
.welcome p{width:840px;margin:16px auto 0;font-size:12px;color:var(--muted)}

/* services */
.services{height:390px;background:var(--soft);border-top:1px solid var(--line);border-bottom:1px solid var(--line)}
.services .wrap{display:flex;justify-content:space-between;padding-top:70px}
.service{width:220px;text-align:center}
.service svg{width:120px;height:120px}
.service h3{font-size:15px;font-weight:700;margin-top:26px;letter-spacing:.5px}
.service p{font-size:12px;color:var(--muted);margin-top:8px}

/* blog */
.recent-blog{height:480px;padding-top:44px}
.section-title{font-size:22px;font-weight:400;text-align:center;letter-spacing:1px;margin-bottom:28px}
.blog-grid{display:flex;gap:16px}
.post{width:238px;border:1px solid var(--line);background:var(--white)}
.post-image{height:170px}
.post-body{padding:14px 14px 10px;height:126px}
.post-body h4{font-size:13px;font-weight:600;color:var(--ink)}
.post-body p{font-size:11px;color:var(--muted);margin-top:6px;line-height:1.55}
.post-meta{border-top:1px solid var(--line);padding:8px 14px;font-size:11px;color:var(--muted);display:flex;justify-content:space-between}

/* middle */
.middle{height:390px;padding-top:40px;border-top:1px solid var(--line)}
.middle .wrap{display:flex;justify-content:space-between}
.label{font-size:14px;font-weight:700;color:var(--blue);letter-spacing:.5px;margin-bottom:16px}
.inspiration{width:260px}
.inspiration-image{height:190px}
.testimonials{width:370px;padding-top:20px}
.testimonials .label{color:var(--ink);font-weight:600}
.quote{font-size:12px;color:var(--muted);line-height:1.7;border-left:3px solid var(--line);padding-left:16px}
.client{display:flex;align-items:center;gap:12px;margin-top:22px}
.client-avatar{width:54px;height:54px;border-radius:50%;background:linear-gradient(135deg,#b7bcc4,#7d8590)}
.client strong{font-size:13px;color:var(--blue);font-weight:600}
.client span{font-size:12px;color:var(--muted)}
.updates{width:280px;height:300px;border:1px solid var(--line);position:relative}
.updates-head{display:flex;justify-content:space-between;align-items:center;padding:12px 14px;border-bottom:1px solid var(--line);font-size:13px;font-weight:600}
.follow{font-size:10px;border:1px solid var(--line);border-radius:3px;padding:1px 8px;background:var(--soft);font-weight:600}
.update{display:flex;gap:10px;padding:16px 24px 16px 14px;border-bottom:1px solid var(--line)}
.update-avatar{width:34px;height:34px;flex:none;border-radius:3px;background:linear-gradient(135deg,#c6cbd2,#8e96a1)}
.update strong{display:block;font-size:11px}
.update em{font-style:normal;font-size:10px;color:var(--muted)}
.update p{font-size:11px;color:var(--muted);margin-top:4px}
.scrollbar{position:absolute;right:4px;top:50px;width:6px;height:120px;border-radius:3px;background:#cfd4da}

/* footer */
.site-footer{height:255px;background:var(--navy);color:#c9d6e3;padding-top:36px}
.site-footer .wrap{display:flex;justify-content:space-between}
.site-footer h5{font-size:14px;font-weight:600;color:var(--white);letter-spacing:.5px;margin-bottom:12px}
.foot-col{font-size:11px;line-height:1.7}
.foot-about{width:200px}
.foot-news{width:240px}
.foot-info{width:140px}
.foot-contact{width:220px}
.social{display:flex;gap:6px;margin-top:12px}
.social i{width:20px;height:20px;background:#c9d6e3;display:block}
.signup{display:flex;margin-top:14px}
.signup span{flex:1;height:30px;background:var(--white);color:var(--muted);padding:6px 10px;font-size:11px}
.signup b{height:30px;padding:6px 12px;background:var(--navy-deep);color:var(--white);font-weight:600;font-size:11px}
.foot-info a{display:block;color:#c9d6e3;text-decoration:none}
.contact-line{display:flex;gap:8px;align-items:flex-start;margin-bottom:6px}
.contact-line svg{width:12px;height:12px;fill:#c9d6e3;flex:none;margin-top:3px}
.copyright{height:45px;background:var(--navy-deep);color:#9fb2c6;font-size:11px;text-align:center;line-height:45px}
</style>
</head>
<body>

<header class="site-header">
  <div class="wrap">
    <div class="brand"><span class="brand-dot"></span>Coralpeak Dynamics</div>
    <nav class="main-nav">
      <a class="active" href="#">HOME</a>
      <a href="#">ABOUT US</a>
      <a href="#">OUR SERVICES</a>
      <a href="#">INSPIRATION</a>
      <a href="#">AVAILABILITY</a>
      <a href="#">BLOG</a>
      <a href="#">CONTACT US</a>
    </nav>
  </div>
</header>

<section class="hero">
  <div class="hero-photo" role="img" aria-label="Overhead photo of a team working together around a meeting table"></div>
  <div class="hero-title">
    <h1>CORALPEAK</h1>
    <p>Dynamics</p>
  </div>
  <svg class="hero-arrow prev" viewBox="0 0 28 28"><path d="M18 6 9 14l9 8z"/></svg>
  <svg class="hero-arrow next" viewBox="0 0 28 28"><path d="M10 6l9 8-9 8z"/></svg>
</section>

<section class="welcome">
  <h2>Welcome To <span>Coralpeak Dynamics</span></h2>
  <p>We help teams deliver better software sooner through agile coaching, consulting, training and facilitation. Our approach is practical, light and tailored to each organisation, whether you are taking first steps or scaling across many teams and departments.</p>
</section>

<section class="services">
  <div class="wrap">
    <div class="service">
      <svg viewBox="0 0 120 120">
        <circle cx="60" cy="60" r="52" fill="#fff" stroke="#e1e4e8" stroke-width="6"/>
        <circle cx="60" cy="60" r="52" fill="none" stroke="var(--red)" stroke-width="6" stroke-dasharray="110 400" transform="rotate(-200 60 60)"/>
        <g fill="var(--red)"><circle cx="50" cy="52" r="7"/><circle cx="70" cy="52" r="7"/><path d="M38 76c0-10 6-15 12-15s12 5 12 15zM58 76c0-10 6-15 12-15s12 5 12 15z"/></g>
      </svg>
      <h3>COACHING</h3>
      <p>Hands-on guidance for teams and leaders adopting agile ways of working every day.</p>
    </div>
    <div class="service">
      <svg viewBox="0 0 120 120">
        <circle cx="60" cy="60" r="52" fill="#fff" stroke="#e1e4e8" stroke-width="6"/>
        <circle cx="60" cy="60" r="52" fill="none" stroke="var(--purple)" stroke-width="6" stroke-dasharray="110 400" transform="rotate(-200 60 60)"/>
        <g fill="var(--purple)"><circle cx="60" cy="54" r="13"/><rect x="53" y="66" width="14" height="10" rx="2"/><rect x="55" y="78" width="10" height="3" rx="1"/></g>
      </svg>
      <h3>CONSULTING</h3>
      <p>Clear assessments and practical roadmaps that improve speed, quality and value of delivery.</p>
    </div>
    <div class="service">
      <svg viewBox="0 0 120 120">
        <circle cx="60" cy="60" r="52" fill="#fff" stroke="#e1e4e8" stroke-width="6"/>
        <circle cx="60" cy="60" r="52" fill="none" stroke="var(--green)" stroke-width="6" stroke-dasharray="110 400" transform="rotate(-200 60 60)"/>
        <g fill="var(--green)"><rect x="44" y="48" width="32" height="28" rx="2"/><circle cx="60" cy="46" r="6"/><circle cx="78" cy="62" r="6"/></g>
      </svg>
      <h3>TRAINING</h3>
      <p>Engaging workshops on Scrum, Kanban and agile fundamentals for every role in teams.</p>
    </div>
    <div class="service">
      <svg viewBox="0 0 120 120">
        <circle cx="60" cy="60" r="52" fill="#fff" stroke="#e1e4e8" stroke-width="6"/>
        <circle cx="60" cy="60" r="52" fill="none" stroke="var(--sky)" stroke-width="6" stroke-dasharray="110 400" transform="rotate(-200 60 60)"/>
        <g fill="var(--sky)"><path d="M58 44a16 16 0 1 0 16 18H58z"/><path d="M62 40v18h16a16 16 0 0 0-16-18z"/></g>
      </svg>
      <h3>FACILITATION</h3>
      <p>Focused planning sessions, retrospectives and events that keep everyone aligned and moving forward.</p>
    </div>
  </div>
</section>

<section class="recent-blog">
  <div class="wrap">
    <h2 class="section-title">RECENT BLOG</h2>
    <div class="blog-grid">
      <article class="post">
        <div class="post-image" role="img" aria-label="Photo of people in a bright meeting room" style="background:linear-gradient(135deg,#dfe3e7,#a9b3bd)"></div>
        <div class="post-body"><h4>Sed docendi copiosae</h4><p>Notes from a recent workshop on shaping backlogs and shared goals.</p></div>
        <div class="post-meta"><span>July 25, 2015</span><span>›</span></div>
      </article>
      <article class="post">
        <div class="post-image" role="img" aria-label="Photo of a laptop and notebook on a wooden desk" style="background:linear-gradient(135deg,#8a6a4e,#3b3230)"></div>
        <div class="post-body"><h4>Sed docendi copiosae</h4><p>Why small batches and quick feedback make teams calmer and faster.</p></div>
        <div class="post-meta"><span>July 25, 2015</span><span>›</span></div>
      </article>
      <article class="post">
        <div class="post-image" role="img" aria-label="Photo of hands working together over a table" style="background:linear-gradient(135deg,#2b3442,#6c7582)"></div>
        <div class="post-body"><h4>Sed docendi copiosae</h4><p>Simple ways to run retrospectives that lead to real change.</p></div>
        <div class="post-meta"><span>July 25, 2015</span><span>›</span></div>
      </article>
      <article class="post">
        <div class="post-image" role="img" aria-label="Photo of business people holding umbrellas" style="background:linear-gradient(180deg,#4e7fa8,#1c2430)"></div>
        <div class="post-body"><h4>Sed docendi copiosae</h4><p>Lessons from leaders starting their first agile transformation this year.</p></div>
        <div class="post-meta"><span>July 25, 2015</span><span>›</span></div>
      </article>
    </div>
  </div>
</section>

<section class="middle">
  <div class="wrap">
    <div class="inspiration">
      <div class="label">INSPIRATION</div>
      <div class="inspiration-image" role="img" aria-label="Photo of a businessman juggling objects against a pale sky" style="background:linear-gradient(180deg,#dfe7ee,#9eabb8)"></div>
    </div>
    <div class="testimonials">
      <div class="label">TESTIMONIALS</div>
      <p class="quote">Working with the team changed how we plan and ship software. Our releases are smoother, our people are happier, and stakeholders finally see steady progress every sprint.</p>
      <div class="client">
        <div class="client-avatar" role="img" aria-label="Client portrait"></div>
        <div><strong>Mara Lindqvist</strong> <span>- Manager</span></div>
      </div>
    </div>
    <aside class="updates">
      <div class="updates-head">Chirpline Updates <span class="follow">Follow</span></div>
      <div class="update">
        <div class="update-avatar"></div>
        <div><strong>Priya Halden</strong><em>@priyahalden</em><p>Great retro session today with the whole team.</p></div>
      </div>
      <div class="update">
        <div class="update-avatar"></div>
        <div><strong>Priya Halden</strong><em>@priyahalden</em><p>Reading about flow metrics and loving the insights.</p></div>
      </div>
      <div class="scrollbar"></div>
    </aside>
  </div>
</section>

<footer class="site-footer">
  <div class="wrap">
    <div class="foot-col foot-about">
      <h5>ABOUT US</h5>
      <p>Coralpeak Dynamics guides software organisations toward faster, better delivery with agile coaching and training.</p>
      <div class="social"><i></i><i></i><i></i><i></i></div>
    </div>
    <div class="foot-col foot-news">
      <h5>JOIN OUR NEWSLETTER</h5>
      <p>Subscribe for fresh ideas, workshop dates and practical agile tips.</p>
      <div class="signup"><span>Email Address</span><b>Subscribe</b></div>
    </div>
    <div class="foot-col foot-info">
      <h5>INFORMATION</h5>
      <a href="#">Home</a><a href="#">Services</a><a href="#">Inspiration</a><a href="#">Availability</a><a href="#">Blog</a><a href="#">Contact</a>
    </div>
    <div class="foot-col foot-contact">
      <h5>CONTACT US</h5>
      <div class="contact-line"><svg viewBox="0 0 12 12"><path d="M6 0a4 4 0 0 0-4 4c0 3 4 8 4 8s4-5 4-8a4 4 0 0 0-4-4zm0 5.5A1.5 1.5 0 1 1 6 2.5a1.5 1.5 0 0 1 0 3z"/></svg><span>1420 Harbor Lane, Suite 210<br>Northvale, CA 90210</span></div>
      <div class="contact-line"><svg viewBox="0 0 12 12"><path d="M2.5 0 4.5 2.5 3.5 4c.8 1.8 2.2 3.2 4 4l1.5-1 2.5 2-1 2.5C5 11.5.5 7 0 1.5z"/></svg><span>+1 (555) 014-2290</span></div>
      <div class="contact-line"><svg viewBox="0 0 12 12"><path d="M0 2h12v8H0zm1 1 5 4 5-4z"/></svg><span>hello@coralpeakdynamics.example</span></div>
    </div>
  </div>
</footer>
<div class="copyright">© Copyright 2015, Coralpeak Dynamics LLC. All Rights Reserved</div>

</body>
</html>
```